Thornvale Group needs a business card design

We need a new business card design using the logo recently selected in a logo competition on Pixel Bazaar. Our business is a consultancy specializing in aviation and energy and the winning business card design will promote an image of precision and professionalism with creativity.

Please use the logo with the name on the front of the card and use a complementary font. Make the back white with either the light grey or dark grey logo.

Target Market(s)

Senior finance and legal leaders at aviation and energy companies

Industry/Entity Type

Management Consulting

Contact Information for Business Card

Peter Castrell
President
Thornvale Group

www.thornvalegroup.example

(555) 204-6391
pc@thornvalegroup.example

Requirements
Must have
• Professional font that goes well with the logo font

```html
<!DOCTYPE html>
<html lang="en">
<head>
<meta charset="utf-8">
<title>Thornvale Group – Business Card</title>
<link rel="stylesheet" href="https://fonts.googleapis.com/css2?family=Montserrat:wght@600;700&family=Mulish:wght@400;600&display=swap">
<style>
  :root {
    --page-bg: #e9e7e3;
    --card-white: #ffffff;
    --brand-blue: #1d4f8f;
    --brand-blue-deep: #123c74;
    --brand-blue-light: #2f63a6;
    --text-grey: #8a8f96;
    --text-on-blue: #ffffff;
    --card-shadow: 0 10px 30px rgba(0, 0, 0, 0.18);
  }
  * { margin: 0; padding: 0; box-sizing: border-box; }
  html, body {
    width: 1200px;
    height: 950px;
    overflow: hidden;
    background: var(--page-bg);
  }
  .canvas {
    position: relative;
    width: 1200px;
    height: 950px;
  }
  .card {
    position: absolute;
    left: 250px;
    width: 700px;
    height: 400px;
    background: var(--card-white);
    box-shadow: var(--card-shadow);
    overflow: hidden;
  }
  .card--front { top: 50px; }
  .card--back { top: 500px; }

  /* Brand lockup (name set as text) */
  .brand {
    display: flex;
    align-items: center;
    gap: 12px;
    color: var(--brand-blue);
    font-family: 'Mulish', sans-serif;
    font-weight: 600;
    letter-spacing: 0.16em;
    text-transform: uppercase;
    white-space: nowrap;
  }
  .brand__square {
    width: 20px;
    height: 20px;
    background: var(--brand-blue);
    flex: none;
  }

  /* Front */
  .front__content {
    position: absolute;
    inset: 0;
    display: flex;
    flex-direction: column;
    align-items: center;
    justify-content: center;
  }
  .front__content .brand { font-size: 22px; margin-bottom: 34px; }
  .holder__name {
    font-family: 'Montserrat', sans-serif;
    font-weight: 700;
    font-size: 22px;
    letter-spacing: 0.06em;
    color: var(--brand-blue);
    text-transform: uppercase;
  }
  .holder__title {
    margin-top: 4px;
    font-family: 'Mulish', sans-serif;
    font-weight: 400;
    font-size: 15px;
    color: var(--text-grey);
    letter-spacing: 0.04em;
  }

  /* Back */
  .back__panel {
    position: absolute;
    inset: 0;
    width: 700px;
    height: 400px;
  }
  .back__brand {
    position: absolute;
    left: 44px;
    top: 150px;
    font-size: 19px;
  }
  .contact {
    position: absolute;
    right: 34px;
    top: 160px;
    list-style: none;
    text-align: right;
    font-family: 'Mulish', sans-serif;
    font-size: 15px;
    line-height: 30px;
    color: var(--text-on-blue);
  }
  .contact__item {
    display: flex;
    justify-content: flex-end;
    align-items: center;
    gap: 12px;
    white-space: nowrap;
  }
  .contact__icon {
    width: 15px;
    height: 15px;
    flex: none;
  }
  .contact__item--plain { padding-right: 27px; }
</style>
</head>
<body>
<main class="canvas">

  <section class="card card--front" aria-label="Card front">
    <div class="front__content">
      <div class="brand"><span class="brand__square"></span>Thornvale Group</div>
      <p class="holder__name">Peter J. Castrell</p>
      <p class="holder__title">President</p>
    </div>
  </section>

  <section class="card card--back" aria-label="Card back">
    <svg class="back__panel" viewBox="0 0 700 400" aria-hidden="true">
      <defs>
        <linearGradient id="panelFill" x1="0" y1="0" x2="1" y2="1">
          <stop offset="0" stop-color="#2f63a6"/>
          <stop offset="0.55" stop-color="#1d4f8f"/>
          <stop offset="1" stop-color="#123c74"/>
        </linearGradient>
      </defs>
      <polygon points="602,0 700,0 700,400 182,400" fill="url(#panelFill)"/>
    </svg>

    <div class="brand back__brand"><span class="brand__square"></span>Thornvale Group</div>

    <ul class="contact">
      <li class="contact__item">(555) 204-6391
        <svg class="contact__icon" viewBox="0 0 16 16" aria-hidden="true"><path fill="#fff" d="M3.6 1.2l2.3 2.6-1.3 1.8c.8 1.9 2.2 3.3 4.1 4.1l1.8-1.3 2.6 2.3-1.2 2.3C7.2 13.4 2.6 8.8 1.3 3.1z"/></svg>
      </li>
      <li class="contact__item">pc@thornvalegroup.example
        <svg class="contact__icon" viewBox="0 0 16 16" aria-hidden="true"><rect x="1" y="3" width="14" height="10" rx="1" fill="#fff"/><path d="M1.5 3.8L8 9l6.5-5.2" fill="none" stroke="#1d4f8f" stroke-width="1.3"/></svg>
      </li>
      <li class="contact__item">www.thornvalegroup.example
        <svg class="contact__icon" viewBox="0 0 16 16" aria-hidden="true"><circle cx="8" cy="8" r="6.5" fill="none" stroke="#fff" stroke-width="1.5"/><ellipse cx="8" cy="8" rx="2.6" ry="6.5" fill="none" stroke="#fff" stroke-width="1.2"/><path d="M1.5 8h13" stroke="#fff" stroke-width="1.2"/></svg>
      </li>
      <li class="contact__item contact__item--plain">Thornvale Group LLC</li>
      <li class="contact__item contact__item--plain">Finance and Strategy Consulting</li>
      <li class="contact__item contact__item--plain">Aviation - Manufacturing - Energy</li>
    </ul>
  </section>

</main>
</body>
</html>
```